One of Australia's fastest growing energy maintenance contractors needs a new website

www.brightleaf.com.au
Our business has evolved over the past years and now our website is no longer relevant.
We clean solar panels and we vacuum roof gutters.
We clean solar panels on the roofs of residential houses right up to billion dollar solar farms with in excess of 1 million panels. We offer thermal image testing and bird proofing for our residential and commercial clients and thermal drone imaging services for our solar farm clients.
We vacuum clean roof gutters (using a LoftSuck) on the residential house next door right up to enormous private and public schools, colleges, shopping centres, strat complexes and commercial buildings.
When first built our business had more of a domestic residential skew and the website reflected that. While that is still part of our core business we are now bidding on and have secured large government, commercial and infrastructure contracts and our new website needs to reflect our growth and our new business. We need a new site that it optimised for both desktop ad phone viewing as our latest figures showed that 73% of people visiting our site are on mobile phones. We have an extensive amount of data on Tallymark Insights available as well as Bidlines. Both that would also need integrating with the site along with a few other plugins such as Quilro Chat IQ, Chatterbox etc along with SEO key words etc. We are also the winner and finalists over multiple years of the small business of the year awards and we like to proudly and prominently display those on our site.
We are looking for a new site with a modern professional feel / theme
There is a definitive break in our business between the solar Panel cleaning clients and the gutter cleaning clients so we would like a home page that begins with a simple choice:
Solar Panel Cleaning – Gutter Cleaning
With a professional full screen background image (we have hundreds to choose from) and along the bottom a small area with rights reserved etc, phone number etc (at some point in the future we will split these into two businesses but for now it’s what we have).
After that selection is made we would like a repeat of that same scenario but the selection is:
If it’s Solar Panel Cleaning
(new background image)
Government – Infrastructure – Commercial – Residential
If it’s Gutter Cleaning
(new background image)
Government – Strata – Commercial – Residential
After making those choices then onto the relevant pages with background images relevant to each sector and a them that suits (on the residential we would like to keep the link to our tallymark reviews) - We will provide copy / text for each relevant page.
Other than that, a menu inclusive of the above and:
Resellers Portal – we will provide a link to this from Quilro CRM)
Customer portal (we will supply a link to this from our booking system)
We also need a page for our Solar Resellers / Partners page but we will give them a link to this, it won’t be listed on the site.
Request a quote page (Again we will provide information from Quilro as this will be linked to the CRM)
Standard contact us page inclusive of phone numbers, address and fields supplied from CRM
Sydney – 02 7391 8056
Southern Highlands – 02 4863 1708
Goulburn – 02 4863 1708
Canberra – 02 6172 4385
Wollongong – 02 4239 5817
sales@brightleaf.com.au
Head Office - Moss Vale NSW 2577
ABN: 48093716552
Responsive Design: Optimized for desktop and mobile (73% mobile visitors).
Fast Loading Speed: Optimized for performance.
Smooth Transition Animations: For service and category selection.
Sticky Contact Bar: Always accessible at the bottom of mobile screens for quick calls.
SEO Optimization: Focused on government tenders, large-scale commercial contracts, and infrastructure projects.
Integrations
Tallymark Insights & Tallymark Bidlines.
Quilro Chat IQ.
Chatterbox Beacon.
SEO tools and keyword optimization.
Many many more images available if needed
Target Market(s)
Residential, commercial, Government

```html
<!DOCTYPE html>
<html lang="en">
<head>
<meta charset="utf-8">
<title>Brightleaf – Home and Service Selection Screens</title>
<link href="https://fonts.googleapis.com/css2?family=Lato:wght@400;700&family=Open+Sans:wght@600;700;800&display=swap" rel="stylesheet">
<style>
:root{
  --page:#ffffff;
  --hero-deep:#1b4596;
  --hero-mid:#2c63bf;
  --hero-soft:#4a86d2;
  --cyan:#1ba6e2;
  --brand-blue:#1f8fd3;
  --ink:#1d1d1d;
  --rule:#cfd6dd;
  --white:#ffffff;
}
*{box-sizing:border-box;margin:0;padding:0}
html,body{width:1200px;height:296px;overflow:hidden;background:var(--page)}
body{position:relative;font-family:"Lato",sans-serif;color:var(--ink)}
.screen{position:absolute;width:391px;height:276px;background:var(--white);box-shadow:0 0 4px rgba(0,0,0,.18);overflow:hidden}
.screen--home{left:6px;top:9px}
.screen--solar{left:405px;top:10px}
.screen--gutter{left:804px;top:11px}
.hero{position:absolute;left:0;top:0;width:391px;height:197px;overflow:hidden}
.hero__photo{position:absolute;inset:0}
.photo--solar-crew{background:linear-gradient(160deg,#3b72c6 0%,#2756ad 45%,#1c438f 100%)}
.photo--gutter-roof{background:linear-gradient(200deg,#5d95d6 0%,#3a74c4 50%,#28599f 100%)}
.photo--single-solar{background:linear-gradient(170deg,#2e5fb3 0%,#1f4a9d 60%,#173c86 100%)}
.photo--single-gutter{background:linear-gradient(160deg,#5a93d4 0%,#3d78c6 55%,#2d61ad 100%)}
.split{position:absolute;top:0;height:197px;width:195.5px}
.split--left{left:0}
.split--right{left:195.5px}
.brand{position:absolute;display:flex;align-items:center;gap:4px;color:var(--white);font-family:"Lato",sans-serif;font-weight:700;font-size:10.5px;letter-spacing:.1px}
.brand__dot{width:7px;height:7px;border-radius:50%;background:var(--white)}
.brand--hero{left:36px;top:38px}
.portal{position:absolute;top:8px;display:flex;gap:6px;right:37px}
.portal__btn{height:17px;padding:0 6px;display:flex;align-items:center;border-radius:2px;font-family:"Lato",sans-serif;font-weight:700;font-size:5.4px;letter-spacing:.1px;white-space:nowrap}
.portal__btn--solid{background:var(--white);color:var(--ink);border:1px solid var(--white)}
.portal__btn--outline{color:var(--white);border:1px solid var(--white)}
.choice{position:absolute;top:155px;color:var(--white);font-family:"Open Sans",sans-serif;font-weight:800;font-size:14.5px;line-height:18px;text-decoration:underline;text-decoration-thickness:1px;text-underline-offset:2px}
.choice--solar{left:37px}
.choice--gutter{left:210px;top:152px}
.hero__title{position:absolute;left:0;right:0;top:88px;text-align:center;color:var(--white);font-family:"Open Sans",sans-serif;font-weight:800;font-size:21.5px;letter-spacing:-.2px}
.sectors{position:absolute;left:0;right:0;top:126px;display:flex;justify-content:center;gap:6px}
.sector{height:17px;padding:0 5px;display:flex;align-items:center;background:var(--cyan);color:var(--white);border-radius:2px;font-family:"Open Sans",sans-serif;font-weight:600;font-size:8px}
.footer{position:absolute;left:0;top:197px;width:391px;height:79px}
.footer__brand{position:absolute;left:36px;top:22px;text-align:center;width:46px}
.footer__brand .brand__name{display:flex;align-items:center;justify-content:center;gap:3px;color:var(--brand-blue);font-weight:700;font-size:6.5px}
.footer__brand .brand__dot{width:9px;height:9px;background:var(--brand-blue);border-radius:50%;margin:0 auto 3px}
.footer__abn{font-size:3.8px;margin-top:2px;white-space:nowrap}
.contact{position:absolute;left:101px;top:22px}
.contact__row{position:absolute;left:0;display:flex;align-items:center;gap:5px;white-space:nowrap;font-size:5.8px}
.contact__row svg{width:8px;height:8px}
.contact__row--loc{top:0}
.contact__row--call{top:12px}
.contact__row--mail{top:25px}
.offices{position:absolute;left:164px;top:24px;font-size:3.8px;white-space:nowrap}
.office{position:absolute;top:0}
.office__phone{position:absolute;top:12px;left:0}
.offices__mail{position:absolute;left:0;top:25px}
.social{position:absolute;left:326px;top:50px;display:flex;gap:3px}
.social__dot{width:7px;height:7px;border-radius:50%;border:0.8px solid var(--brand-blue)}
.social__dot--filled{background:var(--brand-blue)}
.footer__rule{position:absolute;left:36px;width:320px;top:67px;height:0.6px;background:var(--rule)}
.footer__copy{position:absolute;left:0;right:0;top:71px;text-align:center;font-size:3.8px;font-weight:700}
</style>
</head>
<body>

<!-- Home: service choice -->
<section class="screen screen--home">
  <div class="hero">
    <div class="split split--left photo--solar-crew" role="img" aria-label="Worker in hi-vis vest cleaning rooftop solar panels with a long pole brush"></div>
    <div class="split split--right photo--gutter-roof" role="img" aria-label="Worker in blue cap cleaning a roof gutter from a ladder"></div>
    <div class="brand brand--hero"><span class="brand__dot"></span><span>Brightleaf</span></div>
    <div class="portal">
      <span class="portal__btn portal__btn--solid">RESELLERS PORTAL</span>
      <span class="portal__btn portal__btn--outline">CUSTOMER PORTAL</span>
    </div>
    <a class="choice choice--solar">SOLAR PANEL<br>CLEANING</a>
    <a class="choice choice--gutter">GUTTER<br>CLEANING</a>
  </div>
  <footer class="footer">
    <div class="footer__brand"><div class="brand__dot"></div><div class="brand__name">Brightleaf</div><div class="footer__abn"><b>ABN</b> 48093716552</div></div>
    <div class="contact">
      <div class="contact__row contact__row--loc"><svg viewBox="0 0 16 16"><circle cx="8" cy="8" r="8" fill="#1f8fd3"/><path d="M8 3.5a3 3 0 0 0-3 3c0 2.2 3 5.5 3 5.5s3-3.3 3-5.5a3 3 0 0 0-3-3z" fill="#fff"/><circle cx="8" cy="6.5" r="1.1" fill="#1f8fd3"/></svg>Our Location</div>
      <div class="contact__row contact__row--call"><svg viewBox="0 0 16 16"><circle cx="8" cy="8" r="8" fill="#1f8fd3"/><path d="M5.3 4.2l1.4-.3.8 2-1 .8a5 5 0 0 0 2.8 2.8l.8-1 2 .8-.3 1.4c-3.6.4-6.9-2.9-6.5-6.5z" fill="#fff"/></svg>Call Us</div>
      <div class="contact__row contact__row--mail"><svg viewBox="0 0 16 16"><circle cx="8" cy="8" r="8" fill="#1f8fd3"/><rect x="4" y="5" width="8" height="6" rx=".6" fill="#fff"/><path d="M4.3 5.4L8 8.3l3.7-2.9" stroke="#1f8fd3" stroke-width=".8" fill="none"/></svg>Mail Us</div>
    </div>
    <div class="offices">
      <div class="office" style="left:0">Sydney<span class="office__phone">02 7391 8056</span></div>
      <div class="office" style="left:38px">Southern Highlands<span class="office__phone">02 4863 1708</span></div>
      <div class="office" style="left:83px">Goulburn<span class="office__phone">02 4863 1708</span></div>
      <div class="office" style="left:120px">Canberra<span class="office__phone">02 6172 4385</span></div>
      <div class="office" style="left:157px">Wollongong<span class="office__phone">02 4239 5817</span></div>
      <div class="offices__mail">sales@brightleaf.com.au</div>
    </div>
    <div class="social"><span class="social__dot social__dot--filled"></span><span class="social__dot"></span><span class="social__dot"></span></div>
    <div class="footer__rule"></div>
    <div class="footer__copy">Copyright © 2025 Brightleaf . All rights reserved.</div>
  </footer>
</section>

<!-- Solar panel cleaning: sector choice -->
<section class="screen screen--solar">
  <div class="hero">
    <div class="hero__photo photo--single-solar" role="img" aria-label="Crew in hard hats and hi-vis vests cleaning ground-mounted solar panels at a solar farm"></div>
    <div class="brand brand--hero"><span class="brand__dot"></span><span>Brightleaf</span></div>
    <div class="portal">
      <span class="portal__btn portal__btn--solid">RESELLERS PORTAL</span>
      <span class="portal__btn portal__btn--outline">CUSTOMER PORTAL</span>
    </div>
    <h1 class="hero__title">SOLAR PANEL CLEANING</h1>
    <nav class="sectors">
      <span class="sector">Government</span><span class="sector">Infrastructure</span><span class="sector">Commercial</span><span class="sector">Residential</span>
    </nav>
  </div>
  <footer class="footer">
    <div class="footer__brand"><div class="brand__dot"></div><div class="brand__name">Brightleaf</div><div class="footer__abn"><b>ABN</b> 48093716552</div></div>
    <div class="contact">
      <div class="contact__row contact__row--loc"><svg viewBox="0 0 16 16"><circle cx="8" cy="8" r="8" fill="#1f8fd3"/><path d="M8 3.5a3 3 0 0 0-3 3c0 2.2 3 5.5 3 5.5s3-3.3 3-5.5a3 3 0 0 0-3-3z" fill="#fff"/><circle cx="8" cy="6.5" r="1.1" fill="#1f8fd3"/></svg>Our Location</div>
      <div class="contact__row contact__row--call"><svg viewBox="0 0 16 16"><circle cx="8" cy="8" r="8" fill="#1f8fd3"/><path d="M5.3 4.2l1.4-.3.8 2-1 .8a5 5 0 0 0 2.8 2.8l.8-1 2 .8-.3 1.4c-3.6.4-6.9-2.9-6.5-6.5z" fill="#fff"/></svg>Call Us</div>
      <div class="contact__row contact__row--mail"><svg viewBox="0 0 16 16"><circle cx="8" cy="8" r="8" fill="#1f8fd3"/><rect x="4" y="5" width="8" height="6" rx=".6" fill="#fff"/><path d="M4.3 5.4L8 8.3l3.7-2.9" stroke="#1f8fd3" stroke-width=".8" fill="none"/></svg>Mail Us</div>
    </div>
    <div class="offices">
      <div class="office" style="left:0">Sydney<span class="office__phone">02 7391 8056</span></div>
      <div class="office" style="left:38px">Southern Highlands<span class="office__phone">02 4863 1708</span></div>
      <div class="office" style="left:83px">Goulburn<span class="office__phone">02 4863 1708</span></div>
      <div class="office" style="left:120px">Canberra<span class="office__phone">02 6172 4385</span></div>
      <div class="office" style="left:157px">Wollongong<span class="office__phone">02 4239 5817</span></div>
      <div class="offices__mail">sales@brightleaf.com.au</div>
    </div>
    <div class="social"><span class="social__dot social__dot--filled"></span><span class="social__dot"></span><span class="social__dot"></span></div>
    <div class="footer__rule"></div>
    <div class="footer__copy">Copyright © 2025 Brightleaf . All rights reserved.</div>
  </footer>
</section>

<!-- Gutter cleaning: sector choice -->
<section class="screen screen--gutter">
  <div class="hero">
    <div class="hero__photo photo--single-gutter" role="img" aria-label="Worker in a safety harness cleaning a mossy tiled roof and gutter"></div>
    <div class="brand brand--hero"><span class="brand__dot"></span><span>Brightleaf</span></div>
    <div class="portal">
      <span class="portal__btn portal__btn--solid">RESELLERS PORTAL</span>
      <span class="portal__btn portal__btn--outline">CUSTOMER PORTAL</span>
    </div>
    <h1 class="hero__title">GUTTER CLEANING</h1>
    <nav class="sectors">
      <span class="sector">Government</span><span class="sector">Strata</span><span class="sector">Commercial</span><span class="sector">Residential</span>
    </nav>
  </div>
  <footer class="footer">
    <div class="footer__brand"><div class="brand__dot"></div><div class="brand__name">Brightleaf</div><div class="footer__abn"><b>ABN</b> 48093716552</div></div>
    <div class="contact">
      <div class="contact__row contact__row--loc"><svg viewBox="0 0 16 16"><circle cx="8" cy="8" r="8" fill="#1f8fd3"/><path d="M8 3.5a3 3 0 0 0-3 3c0 2.2 3 5.5 3 5.5s3-3.3 3-5.5a3 3 0 0 0-3-3z" fill="#fff"/><circle cx="8" cy="6.5" r="1.1" fill="#1f8fd3"/></svg>Our Location</div>
      <div class="contact__row contact__row--call"><svg viewBox="0 0 16 16"><circle cx="8" cy="8" r="8" fill="#1f8fd3"/><path d="M5.3 4.2l1.4-.3.8 2-1 .8a5 5 0 0 0 2.8 2.8l.8-1 2 .8-.3 1.4c-3.6.4-6.9-2.9-6.5-6.5z" fill="#fff"/></svg>Call Us</div>
      <div class="contact__row contact__row--mail"><svg viewBox="0 0 16 16"><circle cx="8" cy="8" r="8" fill="#1f8fd3"/><rect x="4" y="5" width="8" height="6" rx=".6" fill="#fff"/><path d="M4.3 5.4L8 8.3l3.7-2.9" stroke="#1f8fd3" stroke-width=".8" fill="none"/></svg>Mail Us</div>
    </div>
    <div class="offices">
      <div class="office" style="left:0">Sydney<span class="office__phone">02 7391 8056</span></div>
      <div class="office" style="left:38px">Southern Highlands<span class="office__phone">02 4863 1708</span></div>
      <div class="office" style="left:83px">Goulburn<span class="office__phone">02 4863 1708</span></div>
      <div class="office" style="left:120px">Canberra<span class="office__phone">02 6172 4385</span></div>
      <div class="office" style="left:157px">Wollongong<span class="office__phone">02 4239 5817</span></div>
      <div class="offices__mail">sales@brightleaf.com.au</div>
    </div>
    <div class="social"><span class="social__dot social__dot--filled"></span><span class="social__dot"></span><span class="social__dot"></span></div>
    <div class="footer__rule"></div>
    <div class="footer__copy">Copyright © 2025 Brightleaf . All rights reserved.</div>
  </footer>
</section>

</body>
</html>
```